New Business Card Design Project

Use the flyer uploaded and website www.brightoakbuilders.com for inspiration.
List Our Services on Backside of business cards
Marcus Delling
Harborline Builders Inc.
Licensed General Contractors
858-471-6093

Contact Information for Business Card

Use the flyer uploaded and website www.brightoakbuilders.com for inspiration. List Our Services on Backside of business cards Marcus Delling Harborline Builders Inc. Licensed General Contractors 858-471-6093

```html
<!DOCTYPE html>
<html lang="en">
<head>
<meta charset="utf-8">
<title>Harborline Builders – Business Card</title>
<link rel="stylesheet" href="https://fonts.googleapis.com/css2?family=Cinzel:wght@400&family=Poppins:wght@400;500;700&display=swap">
<style>
  :root{
    --backdrop:#98aeb6;
    --card:#131313;
    --accent:#1a9ad6;
    --ink:#ffffff;
  }
  *{margin:0;padding:0;box-sizing:border-box}
  html,body{width:980px;height:1200px;overflow:hidden;background:var(--backdrop)}
  body{position:relative;font-family:'Poppins',sans-serif;color:var(--ink)}
  .card{position:absolute;left:77px;width:825px;height:471px;background:var(--card);overflow:hidden;box-shadow:0 2px 6px rgba(0,0,0,.25)}
  .card--front{top:131px}
  .card--back{top:629px}
  .frames{position:absolute;inset:0}
  .brand{position:absolute;width:300px;text-align:center;font-family:'Poppins',sans-serif;font-weight:400;font-size:19px;letter-spacing:1px;line-height:1;color:var(--ink)}
  .card--front .brand{left:46px;top:265px}
  .card--back .brand{left:29px;top:262px}
  .holder{position:absolute;left:441px;top:121px;font-family:'Cinzel',serif;font-weight:400;font-size:31px;color:var(--accent);line-height:1}
  .company{position:absolute;left:441px;top:157px;font-size:15px;font-weight:500;letter-spacing:3.3px;line-height:1}
  .rule{position:absolute;left:441px;top:204px;width:85px;height:2px;background:var(--accent)}
  .licence{position:absolute;left:441px;top:235px;font-size:18px;letter-spacing:2.3px;color:var(--accent);line-height:24px}
  .phone{position:absolute;left:441px;top:287px;display:flex;align-items:center;gap:12px;font-size:27px;font-weight:700;line-height:1}
  .phone svg{width:21px;height:21px}
  .web{position:absolute;left:441px;top:321px;font-size:19px;letter-spacing:1.6px;line-height:1}
  .services{position:absolute;list-style:none}
  .services--main{left:383px;top:94px}
  .services--extra{left:635px;top:127px}
  .service{position:relative;padding-left:14px;height:59px;font-size:16px;line-height:19.5px;font-weight:500}
  .service svg{position:absolute;left:-6px;top:3px;width:12px;height:12px}
  .service__name{display:block;color:var(--accent);font-weight:400}
</style>
</head>
<body>

<section class="card card--front" aria-label="Business card front">
  <svg class="frames" viewBox="0 0 825 471" aria-hidden="true">
    <polyline points="825,76 396,76 356,405 825,405" fill="none" stroke="var(--ink)" stroke-width="1.5"/>
    <polyline points="825,62 412,62 375,391 825,391" fill="none" stroke="var(--accent)" stroke-width="1.5"/>
  </svg>
  <div class="brand">Harborline Builders</div>
  <h1 class="holder">Marcus Delling</h1>
  <p class="company">Harborline Builders Inc.</p>
  <div class="rule"></div>
  <p class="licence">LICENSED<br>GENERAL CONTRACTORS</p>
  <p class="phone">
    <svg viewBox="0 0 20 20" aria-hidden="true"><circle cx="10" cy="10" r="10" fill="var(--accent)"/><path d="M6.5 5.5l2 -.3 1 2.3-1.2 1a6 6 0 0 0 3.2 3.2l1-1.2 2.3 1-.3 2c-4.5.5-8.5-3.5-8-8z" fill="var(--ink)"/></svg>
    858-471-6093
  </p>
  <p class="web">www.brightoakbuilders.com</p>
</section>

<section class="card card--back" aria-label="Business card back">
  <svg class="frames" viewBox="0 0 825 471" aria-hidden="true">
    <polyline points="825,59 366,59 325,413 825,413" fill="none" stroke="var(--ink)" stroke-width="1.5"/>
    <polyline points="825,98 620,98 588,374 825,374" fill="none" stroke="var(--accent)" stroke-width="1.5"/>
    <defs>
      <symbol id="tick" viewBox="0 0 12 12"><circle cx="6" cy="6" r="6" fill="var(--accent)"/><path d="M3.3 6.2l1.8 1.7 3.6-3.6" fill="none" stroke="var(--ink)" stroke-width="1.4"/></symbol>
    </defs>
  </svg>
  <div class="brand">Harborline Builders</div>
  <ul class="services services--main">
    <li class="service"><svg><use href="#tick"/></svg><span class="service__name">Remodel:</span>Kitchen &amp; Bath</li>
    <li class="service"><svg><use href="#tick"/></svg><span class="service__name">Painting:</span>Interior &amp; Exterior</li>
    <li class="service"><svg><use href="#tick"/></svg><span class="service__name">Flooring:</span>Carpet, Vinyl, Wood</li>
    <li class="service"><svg><use href="#tick"/></svg><span class="service__name">Window &amp;</span>Door Replacement</li>
    <li class="service"><svg><use href="#tick"/></svg><span class="service__name">Plumbing:</span>Repairs &amp; Upgrades</li>
  </ul>
  <ul class="services services--extra">
    <li class="service"><svg><use href="#tick"/></svg><span class="service__name">Energy-Efficient</span>Upgrades</li>
    <li class="service"><svg><use href="#tick"/></svg><span class="service__name">Deck &amp; Patio</span>Construction</li>
    <li class="service"><svg><use href="#tick"/></svg><span class="service__name">Water &amp;</span>Mold Damage</li>
    <li class="service"><svg><use href="#tick"/></svg><span class="service__name">Garage</span>Renovation</li>
  </ul>
</section>

</body>
</html>
```